Business card design for Quorvane Engineering Tandem

We need a new business card design along with all the necessary to place an order. The company is Quorvane Engineering Tandem and we recently updated our logo.

```html
<!DOCTYPE html>
<html lang="en">
<head>
<meta charset="utf-8">
<title>Quorvane Engineering Tandem – Business Card</title>
<link rel="stylesheet" href="https://fonts.googleapis.com/css2?family=Montserrat:wght@400;600;700&display=swap">
<style>
  :root {
    --backdrop: #3b3b3d;
    --card-white: #ffffff;
    --card-grey: #969695;
    --accent-gold: #e0bb22;
    --brand-grey: #8d8d8d;
    --ink: #333333;
    --emboss: #cfcfcf;
  }
  * { margin: 0; padding: 0; box-sizing: border-box; }
  html, body {
    width: 1200px; height: 1059px; overflow: hidden;
    background: var(--backdrop);
    font-family: "Montserrat", sans-serif;
  }
  .stage { position: relative; width: 1200px; height: 1059px; }
  .card { position: absolute; border-radius: 24px; overflow: hidden; }
  .card-front {
    left: 256px; top: 100px; width: 688px; height: 393px;
    background: var(--card-white);
  }
  .card-back {
    left: 253px; top: 536px; width: 695px; height: 396px;
    background: var(--card-grey);
  }
  .brand {
    position: absolute; display: flex; align-items: center;
    color: var(--brand-grey); font-weight: 600; line-height: 1;
    white-space: nowrap;
  }
  .brand-mark { background: var(--accent-gold); flex: none; }
  .brand-name { display: flex; flex-direction: column; }
  .card-front .brand { left: 59px; top: 162px; gap: 10px; }
  .card-front .brand-mark { width: 24px; height: 24px; }
  .card-front .brand-primary { font-size: 38px; letter-spacing: 2px; }
  .card-front .brand-secondary { font-size: 14.5px; letter-spacing: 1.4px; margin-top: 7px; }
  .divider {
    position: absolute; left: 366px; top: 90px; width: 2px; height: 213px;
    background: var(--accent-gold);
  }
  .details { position: absolute; left: 394px; top: 84px; color: var(--ink); }
  .person-name {
    font-size: 31px; font-weight: 700; color: var(--accent-gold);
    letter-spacing: 0.5px; line-height: 1.1;
  }
  .person-role { font-size: 18.5px; margin-top: 3px; }
  .address { font-size: 18px; line-height: 27.5px; margin-top: 12px; }
  .contacts { list-style: none; margin-top: 9px; font-size: 18px; }
  .contacts li { display: flex; align-items: center; gap: 9px; height: 27.5px; }
  .contacts svg { width: 15px; height: 15px; fill: var(--accent-gold); flex: none; }
  .card-back .brand { left: 72px; top: 130px; gap: 20px; color: var(--emboss); }
  .card-back .brand-mark { width: 42px; height: 42px; background: var(--emboss); }
  .card-back .brand-primary { font-size: 78px; letter-spacing: 3px; }
  .card-back .brand-secondary { font-size: 29px; letter-spacing: 2.6px; margin-top: 10px; }
</style>
</head>
<body>
<main class="stage">
  <section class="card card-front" aria-label="Card front">
    <div class="brand">
      <span class="brand-mark"></span>
      <span class="brand-name">
        <span class="brand-primary">QUORVANE</span>
        <span class="brand-secondary">ENGINEERING TANDEM</span>
      </span>
    </div>
    <div class="divider"></div>
    <div class="details">
      <h1 class="person-name">DANIEL REYES</h1>
      <p class="person-role">Managing Director</p>
      <p class="address">Your address, City<br>State, Zip 1234</p>
      <ul class="contacts">
        <li>
          <svg viewBox="0 0 16 16" aria-hidden="true"><path d="M1 6c0-2 3-3.5 7-3.5S15 4 15 6v1.5h-3.5V6h-7v1.5H1zM4 8h8l2 6H2z"/></svg>
          123 456 789
        </li>
        <li>
          <svg viewBox="0 0 16 16" aria-hidden="true"><path d="M1 3h14v1.5L8 9 1 4.5zM1 6.3l7 4.5 7-4.5V13H1z"/></svg>
          info@quorvane-eng.com
        </li>
        <li>
          <svg viewBox="0 0 16 16" aria-hidden="true"><circle cx="8" cy="8" r="7"/></svg>
          www.quorvane-eng.com
        </li>
      </ul>
    </div>
  </section>

  <section class="card card-back" aria-label="Card back">
    <div class="brand">
      <span class="brand-mark"></span>
      <span class="brand-name">
        <span class="brand-primary">QUORVANE</span>
        <span class="brand-secondary">ENGINEERING TANDEM</span>
      </span>
    </div>
  </section>
</main>
</body>
</html>
```